TALMORK

The business want a professional looking business card. We have a scetch we will add but want the extra upgrade, and would like more suggestions for variations of our business cards.

```html
<!DOCTYPE html>
<html lang="en">
<head>
<meta charset="utf-8">
<title>TALMORK Business Cards</title>
<link rel="stylesheet" href="https://fonts.googleapis.com/css2?family=Marcellus&family=Nunito+Sans:wght@300;400&display=swap">
<style>
  :root {
    --backdrop: #e6e6e6;
    --gold-light: #f1d880;
    --gold-mid: #b8975a;
    --gold-deep: #74522c;
    --foil: #f7e59f;
    --ink-white: #ffffff;
    --card-shadow: rgba(0, 0, 0, 0.22);
  }
  * { margin: 0; padding: 0; box-sizing: border-box; }
  html, body {
    width: 1200px;
    height: 745px;
    overflow: hidden;
    background: var(--backdrop);
  }
  .canvas {
    position: relative;
    width: 1200px;
    height: 745px;
    display: flex;
    align-items: center;
    justify-content: center;
    gap: 50px;
  }
  .card {
    position: relative;
    width: 530px;
    height: 300px;
    border-radius: 3px;
    background: linear-gradient(100deg, var(--gold-light) 0%, var(--gold-mid) 38%, var(--gold-deep) 100%);
    box-shadow: 0 14px 30px var(--card-shadow);
    overflow: hidden;
  }
  /* Front */
  .card-front .brand-lockup {
    position: absolute;
    left: 50%;
    top: 50%;
    transform: translate(-50%, -50%);
    display: flex;
    flex-direction: column;
    align-items: center;
    gap: 14px;
  }
  .brand-dot {
    width: 46px;
    height: 46px;
    border-radius: 50%;
    background: var(--foil);
  }
  .brand-name {
    font-family: "Marcellus", serif;
    color: var(--foil);
    font-size: 34px;
    letter-spacing: 2px;
    line-height: 1;
  }
  /* Back */
  .card-back .holder-title {
    position: absolute;
    left: 40px;
    top: 42px;
    font-family: "Marcellus", serif;
    font-size: 24px;
    letter-spacing: 1.5px;
    color: var(--ink-white);
  }
  .card-back .role {
    position: absolute;
    left: 62px;
    top: 112px;
    font-family: "Nunito Sans", sans-serif;
    font-weight: 300;
    color: var(--ink-white);
  }
  .role-title { font-size: 24px; line-height: 1.1; }
  .role-name { font-size: 13px; margin-top: 2px; }
  .contact-list {
    position: absolute;
    left: 62px;
    top: 190px;
    list-style: none;
    font-family: "Nunito Sans", sans-serif;
    font-weight: 300;
    font-size: 14px;
    color: var(--ink-white);
  }
  .contact-list li {
    display: flex;
    align-items: center;
    gap: 10px;
    height: 24px;
  }
  .contact-list svg {
    width: 14px;
    height: 14px;
    flex: none;
  }
  .card-back .brand-lockup {
    position: absolute;
    right: 40px;
    top: 60px;
    display: flex;
    flex-direction: column;
    align-items: center;
    gap: 10px;
  }
  .card-back .brand-dot { width: 36px; height: 36px; }
  .card-back .brand-name { font-size: 26px; }
</style>
</head>
<body>
<main class="canvas">
  <section class="card card-front" aria-label="Business card front">
    <div class="brand-lockup">
      <span class="brand-dot"></span>
      <span class="brand-name">TALMORK</span>
    </div>
  </section>

  <section class="card card-back" aria-label="Business card back">
    <h1 class="holder-title">TALMORK BREKKESTAD</h1>
    <div class="role">
      <p class="role-title">CEO &amp; Founder</p>
      <p class="role-name">Anders Holm Brekkestad</p>
    </div>
    <ul class="contact-list">
      <li>
        <svg viewBox="0 0 14 14" fill="none" stroke="#fff" stroke-width="1.2"><rect x="3.5" y="1" width="7" height="12" rx="1.3"/><line x1="6" y1="11" x2="8" y2="11"/></svg>
        <span>004791240573</span>
      </li>
      <li>
        <svg viewBox="0 0 14 14" fill="none" stroke="#fff" stroke-width="1.2"><rect x="1" y="3" width="12" height="8" rx="0.8"/><polyline points="1,3 7,8 13,3"/></svg>
        <span>talmork.llc@postbox.cm</span>
      </li>
      <li>
        <svg viewBox="0 0 14 14" fill="none" stroke="#fff" stroke-width="1.1"><circle cx="7" cy="7" r="5.8"/><ellipse cx="7" cy="7" rx="2.6" ry="5.8"/><line x1="1.2" y1="7" x2="12.8" y2="7"/></svg>
        <span>www.talmork.llc</span>
      </li>
    </ul>
    <div class="brand-lockup">
      <span class="brand-dot"></span>
      <span class="brand-name">TALMORK</span>
    </div>
  </section>
</main>
</body>
</html>
```